Floor Inspections and Consulting

We provide inspections and consulting services on various floor coverings, e.g. carpet, hardwood, etc. We also do expert witness work for attorneys due to floor covering failures. We current have a logo, just need it incorporated into a new design. I have examples of cards I have found on the internet that capture my attention and make a statement. I have included our original business card, which in my opinion is terrible, but it does have our logo on it.

```html
<!DOCTYPE html>
<html lang="en">
<head>
<meta charset="utf-8">
<title>Keystone Floor Inspections – Business Card</title>
<link rel="stylesheet" href="https://fonts.googleapis.com/css2?family=Archivo+Black&family=Montserrat:wght@500;700;800&display=swap">
<style>
  :root {
    --backdrop: #d9d9d9;
    --card: #161616;
    --orange: #e8730e;
    --white: #ffffff;
    --muted: #e6e6e6;
  }
  * { box-sizing: border-box; margin: 0; padding: 0; }
  html, body { width: 1200px; height: 1015px; overflow: hidden; }
  body {
    background: var(--backdrop);
    font-family: "Montserrat", Arial, sans-serif;
    position: relative;
  }
  .card {
    position: absolute;
    left: 215px;
    width: 770px;
    height: 440px;
    background: var(--card);
    border-radius: 18px;
    overflow: hidden;
    box-shadow: 0 10px 30px rgba(0,0,0,.25);
  }
  .card--front { top: 50px; }
  .card--back { top: 525px; }

  .tab {
    position: absolute;
    width: 80px;
    height: 62px;
    background: var(--orange);
  }
  .tab--top-right { top: 48px; right: 0; }
  .tab--bottom-left { bottom: 48px; left: 0; }

  .brand {
    display: flex;
    align-items: center;
    gap: 14px;
    font-family: "Montserrat", Arial, sans-serif;
    font-weight: 800;
    color: var(--orange);
    text-transform: uppercase;
    line-height: 1.05;
  }
  .brand__square {
    flex: none;
    width: 46px;
    height: 46px;
    background: var(--orange);
  }
  .card--front .brand {
    position: absolute;
    left: 50%;
    top: 120px;
    transform: translateX(-50%);
    font-size: 30px;
    white-space: nowrap;
  }
  .tagline {
    position: absolute;
    left: 0; right: 0;
    top: 270px;
    text-align: center;
    color: var(--white);
    font-weight: 700;
    font-size: 24px;
    letter-spacing: .2px;
  }

  .card--back .brand {
    position: absolute;
    left: 56px;
    top: 190px;
    font-size: 24px;
    width: 300px;
  }
  .name-band {
    position: absolute;
    right: 0;
    top: 70px;
    width: 390px;
    height: 80px;
    background: var(--orange);
    display: flex;
    align-items: center;
    padding-left: 34px;
    font-family: "Archivo Black", Arial, sans-serif;
    font-size: 25px;
    color: var(--white);
    text-transform: uppercase;
  }
  .contact {
    position: absolute;
    left: 400px;
    top: 188px;
    list-style: none;
    display: flex;
    flex-direction: column;
    gap: 18px;
  }
  .contact__item {
    display: flex;
    align-items: center;
    gap: 14px;
    color: var(--muted);
    font-size: 19px;
    font-weight: 500;
  }
  .contact__icon { width: 24px; height: 24px; flex: none; }
</style>
</head>
<body>

  <section class="card card--front" aria-label="Card front">
    <span class="tab tab--top-right"></span>
    <span class="tab tab--bottom-left"></span>
    <div class="brand">
      <span class="brand__square"></span>
      <span>Keystone Floor<br>Inspections</span>
    </div>
    <p class="tagline">Certified Floor Covering Inspection &amp; Consulting</p>
  </section>

  <section class="card card--back" aria-label="Card back">
    <div class="brand">
      <span class="brand__square"></span>
      <span>Keystone Floor<br>Inspections</span>
    </div>
    <div class="name-band">Daniel Marwick</div>
    <ul class="contact">
      <li class="contact__item">
        <svg class="contact__icon" viewBox="0 0 24 24" aria-hidden="true">
          <rect x="2" y="2" width="20" height="20" rx="4" fill="none" stroke="#e8730e" stroke-width="2"/>
          <path d="M8 6c-1 0-2 1-2 2 0 5 5 10 10 10 1 0 2-1 2-2l-3-2-2 1c-2-1-3-2-4-4l1-2z" fill="#e8730e"/>
        </svg>
        <span>303-555-0142</span>
      </li>
      <li class="contact__item">
        <svg class="contact__icon" viewBox="0 0 24 24" aria-hidden="true">
          <rect x="2" y="5" width="20" height="14" fill="#e8730e"/>
          <path d="M2 5l10 8 10-8" fill="none" stroke="#161616" stroke-width="1.6"/>
        </svg>
        <span>daniel@keystonefloors.com</span>
      </li>
      <li class="contact__item">
        <svg class="contact__icon" viewBox="0 0 24 24" aria-hidden="true">
          <g fill="none" stroke="#e8730e" stroke-width="2">
            <circle cx="12" cy="12" r="10"/>
            <ellipse cx="12" cy="12" rx="4.5" ry="10"/>
            <path d="M2 12h20M4 7h16M4 17h16"/>
          </g>
        </svg>
        <span>www.keystonefloors.com</span>
      </li>
    </ul>
  </section>

</body>
</html>
```